Business Card For Halvenmoor Financial Consulting

Hi, I would like a business card designed. Bold, modern.
Please use the same design as the logo. I have also attached the website design to see the overall theme.
Wordmark Font
Color: Hex: #01AEF7

```html
<!DOCTYPE html>
<html lang="en">
<head>
<meta charset="utf-8">
<title>Halvenmoor Consulting — Business Card</title>
<link rel="stylesheet" href="https://fonts.googleapis.com/css2?family=Poppins:ital,wght@0,400;0,700;1,400&display=swap">
<style>
  :root {
    --stage: #1c1f23;
    --card: #14202b;
    --card-deep: #0f1922;
    --panel: #172633;
    --accent: #01aef7;
    --text: #ffffff;
    --muted: #c9d4dc;
  }
  * { box-sizing: border-box; margin: 0; padding: 0; }
  html, body { width: 1200px; height: 900px; overflow: hidden; }
  body {
    background: var(--stage);
    font-family: "Poppins", sans-serif;
    display: flex;
    flex-direction: column;
    align-items: center;
    justify-content: center;
    gap: 40px;
  }
  .card {
    position: relative;
    width: 640px;
    height: 366px;
    background: var(--card);
    overflow: hidden;
    box-shadow: 0 14px 30px rgba(0,0,0,.45);
  }
  /* Front */
  .brand {
    position: absolute;
    left: 56px; top: 52px;
    display: flex; align-items: center; gap: 14px;
  }
  .brand-square {
    width: 34px; height: 34px;
    border: 3px solid var(--accent);
  }
  .brand-name {
    color: var(--text);
    font-weight: 700;
    font-size: 24px;
    letter-spacing: 2px;
  }
  .address {
    position: absolute;
    left: 56px; top: 132px;
    color: var(--text);
    font-size: 14px;
    line-height: 1.45;
  }
  .contacts {
    position: absolute;
    left: 56px; top: 196px;
    list-style: none;
    color: var(--text);
    font-size: 14px;
    line-height: 1.5;
  }
  .contacts li { display: flex; align-items: center; gap: 8px; }
  .contacts svg { width: 12px; height: 12px; fill: var(--accent); flex: none; }
  .person {
    position: absolute;
    right: 30px; top: 174px;
    text-align: right;
  }
  .person-name {
    color: var(--accent);
    font-weight: 700;
    font-size: 22px;
    letter-spacing: 1px;
  }
  .person-role {
    color: var(--text);
    font-style: italic;
    font-size: 15px;
  }
  .accent-bar {
    position: absolute;
    right: 0; top: 184px;
    width: 10px; height: 44px;
    background: var(--accent);
  }
  .corner-panel {
    position: absolute;
    left: 330px; top: 236px;
    width: 230px; height: 130px;
    background: linear-gradient(160deg, var(--panel) 55%, #3d5b74 100%);
    box-shadow: -6px -6px 14px rgba(0,0,0,.4);
  }
  /* Back */
  .card-back .pattern {
    position: absolute; inset: 0;
    background: linear-gradient(135deg, var(--card) 0%, var(--card-deep) 60%, #1b2d3c 100%);
  }
  .back-brand {
    position: absolute;
    right: 40px; bottom: 36px;
    display: flex; align-items: center; gap: 12px;
  }
  .back-brand .brand-name { color: var(--accent); font-size: 18px; }
  .back-brand .brand-square { width: 26px; height: 26px; }
</style>
</head>
<body>
  <section class="card card-front">
    <div class="brand">
      <span class="brand-square"></span>
      <span class="brand-name">HALVENMOOR CONSULTING</span>
    </div>
    <p class="address">18430 Seacliff Harbor Dr<br>Laguna Cove CA 92651</p>
    <ul class="contacts">
      <li><svg viewBox="0 0 24 24"><path d="M6.6 10.8a15 15 0 0 0 6.6 6.6l2.2-2.2a1 1 0 0 1 1-.25 11.4 11.4 0 0 0 3.6.57 1 1 0 0 1 1 1V20a1 1 0 0 1-1 1A17 17 0 0 1 3 4a1 1 0 0 1 1-1h3.5a1 1 0 0 1 1 1c0 1.25.2 2.45.57 3.57a1 1 0 0 1-.25 1z"/></svg>949-555-0187</li>
      <li><svg viewBox="0 0 24 24"><path d="M2 5h20v14H2z M2 5l10 8 10-8" /></svg>info@HalvenmoorConsulting.com</li>
      <li><svg viewBox="0 0 24 24"><circle cx="12" cy="12" r="10"/></svg>www.HalvenmoorConsulting.com</li>
    </ul>
    <div class="person">
      <p class="person-name">MARCUS TENLEY</p>
      <p class="person-role">President</p>
    </div>
    <span class="accent-bar"></span>
    <div class="corner-panel" role="img" aria-label="Raised square panel with a faint brand graphic"></div>
  </section>

  <section class="card card-back">
    <div class="pattern" role="img" aria-label="Embossed tiled brand pattern in dark navy"></div>
    <div class="back-brand">
      <span class="brand-square"></span>
      <span class="brand-name">HALVENMOOR CONSULTING</span>
    </div>
  </section>
</body>
</html>
```